Velvet Riot Rising Line of Sparkling Wine & Spirits

Back info: Nora Beth Quill Owner 555-318-4402 1480 E. Harlow Ave, Bldg. 2, & 3, Fenwick Ca. 95871
Sparkling Wines & Memorabilia www.velvetriotrising.com
Ok I have uploaded the winning design. The color that I am after is the Fushia, Raspberry, Red, Matte Satin Matalic Finish. With a 24 Karet Gold color Foil. The Bottle is on the top row and it's the 2nd Bottle in. That is the Color that I want. This is the style of font. Make sure that you put what we're advertising. Good Luck to you all. Warmest regards, Nora
21 & up UniSex
Sparkling Wine and Memorabilia
there listed up above.....

```html
<!DOCTYPE html>
<html lang="en">
<head>
<meta charset="utf-8">
<title>Velvet Riot Rising – Business Cards</title>
<link rel="stylesheet" href="https://fonts.googleapis.com/css2?family=Montserrat:wght@400&family=Pinyon+Script&display=swap">
<style>
  :root {
    --backdrop: #c9c9c9;
    --fuchsia: #e0168c;
    --raspberry: #b3106a;
    --raspberry-deep: #9a0c58;
    --gold: #f2cf45;
    --gold-soft: #f7dc6e;
  }
  * { margin: 0; padding: 0; box-sizing: border-box; }
  html, body { width: 1200px; height: 800px; overflow: hidden; }
  body {
    background: var(--backdrop);
    font-family: "Montserrat", sans-serif;
    display: flex;
    align-items: center;
    justify-content: center;
    gap: 40px;
  }
  .card {
    position: relative;
    width: 540px;
    height: 309px;
    border-radius: 4px;
    overflow: hidden;
    color: var(--gold);
    box-shadow: 0 14px 30px rgba(0,0,0,0.28);
  }
  .card--contact {
    background: radial-gradient(ellipse at 45% 55%, var(--fuchsia) 0%, var(--raspberry) 70%, var(--raspberry-deep) 100%);
  }
  .card--brand { background: var(--raspberry); }
  .card__texture {
    position: absolute; inset: 0;
    background: radial-gradient(ellipse at 55% 60%, var(--fuchsia) 0%, var(--raspberry) 65%, var(--raspberry-deep) 100%);
  }
  .wordmark {
    font-family: "Montserrat", sans-serif;
    font-weight: 400;
    color: var(--gold);
    letter-spacing: 0.02em;
    white-space: nowrap;
  }
  .card--contact .wordmark {
    position: absolute; left: 36px; top: 92px; font-size: 27px;
  }
  .holder {
    position: absolute; right: 36px; top: 30px; text-align: right;
  }
  .holder__name {
    font-family: "Pinyon Script", cursive;
    font-size: 34px; line-height: 1.1; color: var(--gold-soft);
    padding-right: 4px;
  }
  .holder__title { font-size: 13px; color: var(--gold-soft); margin-top: 2px; }
  .contact-list {
    position: absolute; left: 36px; top: 160px;
    list-style: none; font-size: 13.5px; line-height: 1.55; color: var(--gold-soft);
  }
  .contact-list li { display: flex; align-items: center; gap: 8px; }
  .contact-list svg { width: 12px; height: 12px; flex: none; }
  .icon-cut { stroke: var(--raspberry); }
  .address {
    position: absolute; left: 36px; bottom: 28px;
    font-size: 13.5px; line-height: 1.45; color: var(--gold-soft); font-style: normal;
  }
  .card--brand .wordmark {
    position: absolute; left: 0; right: 0; top: 118px;
    text-align: center; font-size: 34px;
  }
  .tagline {
    position: absolute; left: 0; right: 0; bottom: 56px;
    text-align: center; font-size: 13px; letter-spacing: 0.08em;
    text-transform: uppercase; color: var(--gold-soft);
  }
</style>
</head>
<body>
  <section class="card card--contact">
    <div class="wordmark">Velvet Riot Rising</div>
    <div class="holder">
      <div class="holder__name">Nora Beth Quill</div>
      <div class="holder__title">Owner</div>
    </div>
    <ul class="contact-list">
      <li>
        <svg viewBox="0 0 12 12" aria-hidden="true"><path d="M2.5 1h2l1 2.6-1.3 1a6 6 0 0 0 3.2 3.2l1-1.3L11 7.5v2A1.5 1.5 0 0 1 9.5 11 8.5 8.5 0 0 1 1 2.5 1.5 1.5 0 0 1 2.5 1z" fill="currentColor"/></svg>
        555-318-4402
      </li>
      <li>
        <svg viewBox="0 0 12 12" aria-hidden="true"><rect x="0.5" y="2" width="11" height="8" fill="currentColor"/><path class="icon-cut" d="M0.8 2.4 6 6.6l5.2-4.2" stroke-width="1" fill="none"/></svg>
        hello@velvetriotrising.com
      </li>
      <li>
        <svg viewBox="0 0 12 12" aria-hidden="true"><circle cx="6" cy="6" r="5.5" fill="currentColor"/><path class="icon-cut" d="M0.5 6h11M6 0.5c-2.4 2.8-2.4 8.2 0 11M6 0.5c2.4 2.8 2.4 8.2 0 11" stroke-width="0.8" fill="none"/></svg>
        www.velvetriotrising.com
      </li>
    </ul>
    <address class="address">
      1480 E. Harlow Ave<br>
      Bldg. 2, &amp; 3, Fenwick Ca. 95871
    </address>
  </section>

  <section class="card card--brand">
    <div class="card__texture" role="img" aria-label="Fuchsia satin background with a subtle tonal ornamental pattern"></div>
    <div class="wordmark">Velvet Riot Rising</div>
    <p class="tagline">Sparkling Wines &amp; Memorabilia</p>
  </section>
</body>
</html>
```